Business Card Design For Marketing Agnecy LVP

Need business card design for marketing agency.

Doug Fenwick
President, CEO
1-555-302-4196
doug@boldpromoperksgroup.example
www.BoldPromoPerksGroup.example

Back Side:
Boost Sales Using Rewards, Incentives & Giveaways
Get A Free Sample Package

Target Market(s)

B2B

Industry/Entity Type

Marketing

Contact Information for Business Card

Doug Fenwick
President, CEO
1-555-302-4196

Back Side:
Get A Free Sample Package

Please note that my current url is OLD DESIGN. I am working on new design and want the business card to match color themes at least on new site. Here is the demo link for new site so you can see the colors I use, etc.

http://layoutcratehub.example/kq/doug/lvp_final/index.html

Requirements
Must have
• Please note that my current url is OLD DESIGN. I am working on new design and want the business card to match color themes at least on new site. Here is the demo link for new site so you can see the colors I use, etc.

Nice to have

Should not have

```html
<!DOCTYPE html>
<html lang="en">
<head>
<meta charset="UTF-8">
<title>LVP Business Card</title>
<link href="https://fonts.googleapis.com/css2?family=Montserrat:wght@300;400;700;800&family=Arimo:wght@400;700&display=swap" rel="stylesheet">
<style>
  :root {
    --brand-blue: #0f76bf;
    --brand-grey: #515256;
    --paper: #ffffff;
    --backdrop: #d9dadc;
    --ink-light: #ffffff;
  }
  * { box-sizing: border-box; margin: 0; padding: 0; }
  html, body { width: 1200px; height: 900px; overflow: hidden; }
  body {
    background: var(--backdrop);
    font-family: "Arimo", Arial, sans-serif;
    position: relative;
  }
  .card {
    position: absolute;
    left: 290px;
    width: 620px;
    height: 354px;
    overflow: hidden;
    box-shadow: 0 10px 24px rgba(0,0,0,0.25);
  }
  .card--back { top: 76px; background: var(--brand-blue); color: var(--ink-light); }
  .card--front { top: 470px; background: var(--brand-blue); color: var(--ink-light); }

  /* Back side */
  .back-logo {
    position: absolute; left: 120px; top: 112px; width: 150px;
    display: flex; align-items: center; gap: 10px;
    font-family: "Montserrat", sans-serif; font-weight: 800;
    font-size: 50px; letter-spacing: 1px; color: var(--ink-light);
  }
  .logo-dot { width: 14px; height: 14px; border-radius: 50%; background: currentColor; flex: none; }
  .back-divider {
    position: absolute; left: 300px; top: 92px; width: 1px; height: 110px;
    background: var(--ink-light);
  }
  .back-benefits {
    position: absolute; left: 326px; top: 108px; list-style: none;
    font-family: "Montserrat", sans-serif; font-weight: 400; font-size: 17px;
    line-height: 27px; letter-spacing: 0.4px;
  }
  .back-benefits li::before { content: "\2022"; margin-right: 6px; }
  .back-url {
    position: absolute; left: 0; right: 0; bottom: 40px; text-align: center;
    font-size: 16px; letter-spacing: 0.3px;
  }

  /* Front side */
  .front-shape { position: absolute; inset: 0; }
  .front-logo {
    position: absolute; left: 40px; top: 150px;
    display: flex; align-items: center; gap: 10px;
    font-family: "Montserrat", sans-serif; font-weight: 800;
    font-size: 58px; letter-spacing: 1px; color: var(--brand-blue);
  }
  .contact-block { position: absolute; left: 360px; top: 88px; right: 18px; }
  .contact-name {
    font-family: "Arimo", sans-serif; font-weight: 700; font-size: 20px;
    text-transform: uppercase; letter-spacing: 0.3px;
  }
  .contact-title { font-size: 15px; margin-top: 2px; }
  .contact-rule { width: 130px; height: 1px; background: var(--ink-light); margin: 14px 0 12px; }
  .contact-list { list-style: none; font-size: 13px; line-height: 23px; }
  .contact-list li { display: flex; align-items: center; gap: 8px; white-space: nowrap; }
  .contact-icon {
    width: 14px; height: 14px; background: var(--ink-light); border-radius: 2px;
    display: inline-flex; align-items: center; justify-content: center; flex: none;
  }
</style>
</head>
<body>

<section class="card card--back" aria-label="Card back">
  <div class="back-logo"><span class="logo-dot"></span>LVP</div>
  <div class="back-divider"></div>
  <ul class="back-benefits">
    <li>Boost Sales Using Rewards</li>
    <li>Incentives &amp; Giveaways</li>
    <li>Get A Free Sample Package</li>
  </ul>
  <p class="back-url">www.BoldPromoPerksGroup.example</p>
</section>

<section class="card card--front" aria-label="Card front">
  <svg class="front-shape" width="620" height="354" viewBox="0 0 620 354" aria-hidden="true">
    <path d="M0 0 H215 C298 55 342 195 338 354 H0 Z" fill="var(--brand-grey)"/>
    <path d="M0 0 H190 C272 52 316 192 310 354 H0 Z" fill="var(--paper)"/>
  </svg>
  <div class="front-logo"><span class="logo-dot"></span>LVP</div>

  <div class="contact-block">
    <p class="contact-name">Doug Fenwick</p>
    <p class="contact-title">President, CEO</p>
    <div class="contact-rule"></div>
    <ul class="contact-list">
      <li>
        <span class="contact-icon">
          <svg width="10" height="10" viewBox="0 0 24 24"><path fill="var(--brand-blue)" d="M6.6 10.8a15 15 0 0 0 6.6 6.6l2.2-2.2c.3-.3.7-.4 1-.2 1.1.4 2.3.6 3.6.6.6 0 1 .4 1 1V20c0 .6-.4 1-1 1A17 17 0 0 1 3 4c0-.6.4-1 1-1h3.5c.6 0 1 .4 1 1 0 1.3.2 2.5.6 3.6.1.3 0 .7-.2 1z"/></svg>
        </span>1-555-302-4196
      </li>
      <li>
        <span class="contact-icon">
          <svg width="10" height="10" viewBox="0 0 24 24"><rect x="2" y="5" width="20" height="14" fill="none" stroke="var(--brand-blue)" stroke-width="2"/><path d="M2 5l10 8 10-8" fill="none" stroke="var(--brand-blue)" stroke-width="2"/></svg>
        </span>doug@boldpromoperksgroup.example
      </li>
      <li>
        <span class="contact-icon">
          <svg width="10" height="10" viewBox="0 0 24 24"><circle cx="12" cy="12" r="9" fill="none" stroke="var(--brand-blue)" stroke-width="2"/><path d="M3 12h18M12 3c3 3 3 15 0 18M12 3c-3 3-3 15 0 18" fill="none" stroke="var(--brand-blue)" stroke-width="1.6"/></svg>
        </span>www.BoldPromoPerksGroup.example
      </li>
    </ul>
  </div>
</section>

</body>
</html>
```